NZ First of it's kind solutions directory and marketplace for busy Mums needs a business card design

We need a business card design for our new nationwide business in NZ (long term plans to go global). We provide solutions to the everyday challenges that busy Mums face by connecting them with quality communities and suppliers of carefully selected, relevant products and services. We sell direct via our online marketplace. The final design should communicate our values of inclusivity, quality and smart solutions. Colours should incorporate our logo colour palette of #477077 and #6ba8b2. Our website is at https://www.brightnestmums.example

Target Market(s)

busy Mums, Age 28 – 50, female, income over $100K, location main centres NZ primarily but NZ wide. Is likely juggling work or career with a young family. Probably had hobbies which have fallen by the wayside.
-Wants to succeed in her chosen career without compromising on family life
-to successfully juggle her career without feeling like she is compromising her children
- Is time poor, something always has to give and it’s generally her health (she’ll stay up late, get stressed)
- probably ex corporate or professional career. Has discretional income

Industry/Entity Type

Business

Contact Information for Business Card

Lena Forbisher, Founder, BrightNestMums.example (Strapline Tap; Gather; Sorted), 47 Kowhai Terrace, Ellerslie, Auckland 1051, New Zealand. Mob: 021 483 517 Ph: +64 (0)9 571 4860

Font styles to use
Other font styles liked:
• Raleway, and/or Architects Daughter

Colors
00a990
33b8a4
86cfc6
cfeae6

Requirements
Must have
• the above details, streamline. the logo and colours associated with those logos
Should not have
• foil or metallic colours

```html
<!DOCTYPE html>
<html lang="en">
<head>
<meta charset="utf-8">
<title>BrightNestMums business card</title>
<link href="https://fonts.googleapis.com/css2?family=Raleway:wght@400;500;600;800&display=swap" rel="stylesheet">
<style>
  :root {
    --teal-deep: #477077;
    --teal-light: #6ba8b2;
    --ink: #1c2527;
    --text-grey: #4a4f51;
    --paper: #ffffff;
    --stage: #e9ecec;
    --mark-faint: #f3f4f4;
  }
  * { box-sizing: border-box; margin: 0; padding: 0; }
  html, body {
    width: 1200px; height: 880px; overflow: hidden;
    background: var(--stage);
    font-family: "Raleway", sans-serif;
  }
  .canvas {
    position: relative; width: 1200px; height: 880px;
  }
  .card {
    position: absolute; width: 700px; height: 400px;
    border-radius: 26px; overflow: hidden;
    box-shadow: 0 10px 28px rgba(0,0,0,0.18);
  }
  .card--front { left: 150px; top: 30px; background: var(--teal-deep); }
  .card--back { left: 350px; top: 450px; background: var(--paper); }

  .wordmark {
    position: absolute; display: flex; align-items: center; gap: 16px;
    font-weight: 800; letter-spacing: -1px; white-space: nowrap;
  }
  .wordmark__dot { border-radius: 50%; flex: none; }

  .card--front .wordmark { left: 50%; top: 50%; transform: translate(-50%, -50%); font-size: 54px; color: var(--ink); }
  .card--front .wordmark__dot { width: 52px; height: 52px; background: var(--ink); }

  .card--back .faint-circle {
    position: absolute; right: -70px; top: -40px; width: 340px; height: 340px;
    border-radius: 50%; background: var(--mark-faint);
  }
  .card--back .wordmark { left: 60px; top: 74px; font-size: 50px; color: var(--teal-deep); }
  .card--back .wordmark__dot { width: 50px; height: 50px; background: var(--teal-deep); }
  .strapline {
    position: absolute; left: 300px; top: 138px;
    font-size: 17px; font-weight: 500; color: var(--text-grey); letter-spacing: 0.5px;
  }

  .contact { position: absolute; left: 60px; top: 220px; color: var(--text-grey); }
  .contact__name { font-size: 24px; font-weight: 800; letter-spacing: -0.5px; }
  .contact__name .first { color: var(--teal-deep); }
  .contact__name .last { color: var(--teal-light); font-weight: 600; }
  .contact__role { font-size: 17px; font-weight: 500; margin-bottom: 14px; }
  .contact__address { font-size: 16px; font-weight: 500; line-height: 1.35; margin-bottom: 10px; }
  .contact__row { display: flex; gap: 34px; font-size: 16px; font-weight: 500; margin-bottom: 6px; }
  .contact__item { display: flex; align-items: center; gap: 8px; }
  .contact__icon { width: 20px; height: 20px; flex: none; }
  .contact__web .domain { color: var(--teal-light); }
</style>
</head>
<body>
<main class="canvas">
  <section class="card card--front" aria-label="Card front">
    <div class="wordmark"><span class="wordmark__dot"></span>BrightNestMums</div>
  </section>

  <section class="card card--back" aria-label="Card back">
    <div class="faint-circle"></div>
    <div class="wordmark"><span class="wordmark__dot"></span>BrightNestMums</div>
    <p class="strapline">Tap | Gather | Sorted</p>

    <div class="contact">
      <p class="contact__name"><span class="first">Lena</span><span class="last">Forbisher</span></p>
      <p class="contact__role">Founder</p>
      <p class="contact__address">47 Kowhai Terrace<br>Ellerslie, Auckland 1051, New Zealand</p>
      <div class="contact__row">
        <span class="contact__item">
          <svg class="contact__icon" viewBox="0 0 20 20" aria-hidden="true">
            <circle cx="10" cy="10" r="9" fill="none" stroke="#6ba8b2" stroke-width="1.4"/>
            <rect x="7" y="4.5" width="6" height="11" rx="1.2" fill="none" stroke="#6ba8b2" stroke-width="1.3"/>
          </svg>021 483 517
        </span>
        <span class="contact__item">
          <svg class="contact__icon" viewBox="0 0 20 20" aria-hidden="true">
            <circle cx="10" cy="10" r="9" fill="none" stroke="#6ba8b2" stroke-width="1.4"/>
            <path d="M5.5 8.5c1-2 8-2 9 0l-1.5 1.2h-1.5l-.5-1.2h-3l-.5 1.2H6.5z" fill="#6ba8b2"/>
            <rect x="6.5" y="10.5" width="7" height="4" rx="1" fill="#6ba8b2"/>
          </svg>+64 (0)9 571 4860
        </span>
      </div>
      <div class="contact__row">
        <span class="contact__item contact__web">
          <svg class="contact__icon" viewBox="0 0 20 20" aria-hidden="true">
            <circle cx="10" cy="10" r="9" fill="none" stroke="#6ba8b2" stroke-width="1.4"/>
            <circle cx="10" cy="10" r="5.5" fill="none" stroke="#6ba8b2" stroke-width="1.1"/>
            <path d="M4.5 10h11M10 4.5v11M10 4.5c-2.5 3-2.5 8 0 11M10 4.5c2.5 3 2.5 8 0 11" fill="none" stroke="#6ba8b2" stroke-width="1"/>
          </svg>www.<span class="domain">brightnestmums</span>.example
        </span>
      </div>
    </div>
  </section>
</main>
</body>
</html>
```